tinyTally Resource Book - 10 maths tasks to do outside

I need a 22 (11 pages back to back) page A6 sized book produced to standard for submission to professional printer. Needs to be as .pdf file showing guide lines and allowances for colour bleed. I have text already written and submitted as attachment in a Word file with margins set to A6 size. The theme of the materials is "Nature Play" so using lots of pictures from nature (Australia preferably) and showing lots of patterns in nature (rocks, leaves, flower petals etc). Some of the tasks refer to specific activities, such as "shadows" and "floating" so would be great to illustrate appropriately. The big emphasis is on learning outside the classroom, getting kids to engage actively with nature. I would like to see the pages as full colour - so not white background. The book itself will be spiral bound along the top edge so a margin of at least 1cm will be required at the top of each page (or the bottom of even numbered pages). Book will be printed on plastic laminated matte paper for outdoor use. Font size needs to be big enough to read. Fonts sizes, alignments and page numbers are all different at the moment and need to be standardised. One photo is included in a page as a sample if you can use it, otherwise disregard. Logo for Wattlebrook Numeracy Guild is also included to have as part of the acknowledgements at the back of the book.

Target Market(s)

Book is for early childhood and preschool teachers.

Industry/Entity Type

Education

Font styles to use
Sans Serif

Requirements
Must have
• Colour and appeal.
Nice to have
• Use of natural colours instead of bright catchy colours but that is your call.
Should not have
• American spelling

```html
<!DOCTYPE html>
<html lang="en-AU">
<head>
<meta charset="utf-8">
<title>10. Repeat My Pattern</title>
<link rel="stylesheet" href="https://fonts.googleapis.com/css2?family=Baloo+2:wght@800&family=Jost:wght@400&display=swap">
<style>
  :root {
    --paper: #ffffff;
    --sand-light: #d9a58a;
    --sand-mid: #c98f74;
    --sand-dark: #b87a62;
    --heading-blue: #2f3e8e;
    --heading-edge: #ffffff;
    --body-ink: #352a27;
    --bullet-red: #e0262b;
    --badge-blue: #2f3e8e;
    --badge-text: #ffffff;
    --trim-line: #6b6b6b;
    --shell-tone: #d89a52;
    --nut-tone: #b9652c;
  }
  * { margin: 0; padding: 0; box-sizing: border-box; }
  html, body { width: 892px; height: 1200px; overflow: hidden; background: var(--paper); }
  .page {
    position: relative; width: 892px; height: 1200px; background: var(--paper);
    font-family: "Jost", "Futura", sans-serif; color: var(--body-ink);
  }
  .trim-marks { position: absolute; inset: 0; }
  .bleed-area {
    position: absolute; left: 52px; top: 52px; width: 788px; height: 1096px;
    background:
      repeating-linear-gradient(100deg, rgba(255,220,190,0.14) 0 5px, rgba(150,90,70,0.08) 5px 38px, transparent 38px 66px),
      linear-gradient(160deg, var(--sand-light), var(--sand-mid) 55%, var(--sand-dark));
  }
  .heading {
    position: absolute; left: 125px;
    font-family: "Baloo 2", "Arial Rounded MT Bold", sans-serif; font-weight: 800;
    color: var(--heading-blue); line-height: 1;
    text-shadow: -1.5px -1.5px 0 var(--heading-edge), 1.5px -1.5px 0 var(--heading-edge),
                 -1.5px 1.5px 0 var(--heading-edge), 1.5px 1.5px 0 var(--heading-edge),
                 3px 3px 2px rgba(0,0,0,0.25);
  }
  .task-title { top: 138px; font-size: 58px; letter-spacing: 0.5px; }
  .section-title { font-size: 46px; }
  .list { position: absolute; left: 218px; width: 530px; list-style: none; font-size: 34px; line-height: 42.5px; }
  .list li { position: relative; }
  .list li::before {
    content: ""; position: absolute; left: -30px; top: 14px; width: 16px; height: 16px;
    background: var(--bullet-red); transform: rotate(45deg);
  }
  .list-tasks { top: 200px; }
  .list-questions { top: 448px; }
  .list-variations { top: 656px; width: 455px; }
  .list-ideas { top: 905px; width: 180px; }
  .pattern-photo {
    position: absolute; left: 360px; top: 913px; width: 340px; height: 66px;
    transform: rotate(-27deg); transform-origin: center;
    border-radius: 33px;
    background: linear-gradient(90deg, var(--nut-tone), var(--shell-tone), var(--nut-tone), var(--shell-tone));
    opacity: 0.85;
  }
  .page-number { position: absolute; left: 694px; top: 1021px; width: 74px; height: 70px; }
</style>
</head>
<body>
<div class="page">
  <svg class="trim-marks" width="892" height="1200" viewBox="0 0 892 1200" aria-hidden="true">
    <g stroke="var(--trim-line)" stroke-width="1" fill="none">
      <path d="M52 0V34M0 52H34M74 36V74H36"/>
      <path d="M840 0V34M892 52H858M818 36V74H856"/>
      <path d="M52 1200V1166M0 1148H34M74 1164V1126H36"/>
      <path d="M840 1200V1166M892 1148H858M818 1164V1126H856"/>
    </g>
  </svg>

  <div class="bleed-area" role="img" aria-label="Rippled desert sand background"></div>

  <h1 class="heading task-title">10. Repeat My Pattern</h1>
  <ul class="list list-tasks">
    <li>Make a pattern from your choice of materials</li>
    <li>Ask partner to continue the pattern</li>
    <li>Swap roles with partner</li>
  </ul>

  <h2 class="heading section-title" style="top:396px">Prompting questions</h2>
  <ul class="list list-questions">
    <li>Can you keep the same objects but introduce a new object into your pattern?</li>
  </ul>

  <h2 class="heading section-title" style="top:603px">Variations</h2>
  <ul class="list list-variations">
    <li>Change the pattern – partner removes something from your original pattern then continues on with the new pattern</li>
  </ul>

  <h2 class="heading section-title" style="top:852px">Big Ideas</h2>
  <ul class="list list-ideas">
    <li>Attributes</li>
    <li>Building on a pattern</li>
    <li>Repeat</li>
  </ul>

  <div class="pattern-photo" role="img" aria-label="Photo of hazelnuts and cockle shells laid in a repeating line"></div>

  <svg class="page-number" viewBox="0 0 74 70" aria-label="Page 21">
    <polygon points="37,1 73,27 59,69 15,69 1,27" fill="var(--badge-blue)"/>
    <text x="37" y="53" text-anchor="middle" font-family="Jost, sans-serif" font-size="34" fill="var(--badge-text)">21</text>
  </svg>
</div>
</body>
</html>
```